Lumen Fitness Personal Training Business

I need a business card design with a logo for my personal training company. I'd like the colors to be a vibrant green and black. I'd like the logo to incorporate an anvil (or something similar). I train hardcore competitive athletes as well as soccer moms trying to get and/or stay in shape. I need a logo that will not pigeon hole me in one category or the other, but at the same time not be too intimidating to soccer moms, but will not be off putting to the more hardcore trainees. The design should be attention grabbing and aesthetic.
Target Market(s)
Hardcore athletes as well as average people just trying to get/stay in shape.
Industry/Entity Type
Training

```html
<!DOCTYPE html>
<html lang="en">
<head>
<meta charset="utf-8">
<title>Lumen Fitness – Business Card</title>
<link rel="stylesheet" href="https://fonts.googleapis.com/css2?family=Alegreya:wght@400;700&display=swap">
<style>
  :root {
    --canvas: #e9e6e1;
    --card: #050505;
    --green: #4cc45a;
    --green-deep: #1faa55;
    --white: #f2f2f2;
    --shadow: rgba(0, 0, 0, 0.28);
  }
  * { box-sizing: border-box; margin: 0; padding: 0; }
  html, body {
    width: 1200px;
    height: 900px;
    overflow: hidden;
    background: var(--canvas);
    font-family: "Alegreya", Georgia, serif;
  }
  .sheet {
    width: 1200px;
    height: 900px;
    display: flex;
    flex-direction: column;
    align-items: center;
    justify-content: center;
    gap: 36px;
  }
  .card {
    position: relative;
    width: 700px;
    height: 400px;
    background: var(--card);
    box-shadow: 0 10px 28px var(--shadow);
  }
  /* Front */
  .card-front {
    display: flex;
    align-items: center;
    justify-content: center;
  }
  .brand {
    display: flex;
    align-items: center;
    gap: 16px;
    color: var(--green);
    font-weight: 700;
    text-transform: uppercase;
    letter-spacing: 0.02em;
  }
  .brand-mark {
    background: var(--green);
    flex: none;
  }
  .brand-front { font-size: 58px; }
  .brand-front .brand-mark { width: 40px; height: 40px; }
  /* Back */
  .brand-back {
    position: absolute;
    top: 92px;
    right: 42px;
    font-size: 34px;
    gap: 12px;
  }
  .brand-back .brand-mark { width: 24px; height: 24px; }
  .holder {
    position: absolute;
    left: 44px;
    top: 188px;
  }
  .holder-name {
    color: var(--green);
    font-size: 32px;
    font-weight: 400;
    line-height: 1.05;
  }
  .holder-role {
    color: var(--white);
    font-size: 17px;
    margin-top: 2px;
  }
  .contact {
    position: absolute;
    left: 44px;
    top: 282px;
    color: var(--white);
    font-size: 17px;
    line-height: 1.55;
  }
  .contact .label { color: var(--green); }
  .contact .web { color: var(--green); }
  .contact span + span { margin-left: 10px; }
</style>
</head>
<body>
  <main class="sheet">
    <section class="card card-front" aria-label="Card front">
      <div class="brand brand-front">
        <span class="brand-mark"></span>
        <span class="brand-name">Lumen Fitness</span>
      </div>
    </section>

    <section class="card card-back" aria-label="Card back">
      <div class="brand brand-back">
        <span class="brand-mark"></span>
        <span class="brand-name">Lumen Fitness</span>
      </div>

      <div class="holder">
        <h1 class="holder-name">Daniel Reeve</h1>
        <p class="holder-role">Managing Director</p>
      </div>

      <address class="contact">
        <p>48, Harrow Lane, Eastfield, 20417</p>
        <p>
          <span><span class="label">T:</span> (021) 555 0148</span>
          <span><span class="label">F:</span> (021) 5550149</span>
          <span><span class="label">M:</span> (021) 5550150</span>
        </p>
        <p>
          <span><span class="label">E:</span> hello@lumenfit.com</span>
          <span class="web">www.lumenfit.com</span>
        </p>
      </address>
    </section>
  </main>
</body>
</html>
```